Business cards for 3 Realtors at one brokerage

We will need a business card template that can be projected on 3 business cards. Harborline Realty & Investment Corp. has 3 realtors on staff Dane, Owen, and Miles. We all want a business card that shows our new logo and information. I will attach many versions of our Logo as well as head shots for each realtor (Owen- Long hair, youngest. Miles- Suit jacket, parted hair cut. Dane- Angled Pose, Shirt and Tie.) I have attached our information below.

Dane Foskett
801-555-0147
dane@harborlinehomesite.com
Principal Broker

Miles Tandrow
801-555-0162
miles@harborlinehomesite.com
Real Estate Agent

Owen Tandrow
801-555-0138
owen@harborlinehomesite.com
Real Estate Agent

Harborline Realty & Investment Corp.
HarborlineHomesite.com
5286 N 7200 Suite 208-617, South Jordan, UT 84009

Please feel free to reach out with any questions, comments, or concerns.

```html
<!DOCTYPE html>
<html lang="en">
<head>
<meta charset="utf-8">
<title>Harborline Realty – Business Cards</title>
<link href="https://fonts.googleapis.com/css2?family=Montserrat:wght@400;600;700&display=swap" rel="stylesheet">
<style>
  :root {
    --backdrop: #bdbdbd;
    --card: #1b1c1e;
    --edge: #2e9be6;
    --accent: #33a7f0;
    --silver: #c9cbce;
    --muted: #8a8c90;
    --text: #e4e5e7;
    --photo-top: #c9c7c9;
    --photo-bottom: #8f9096;
  }
  * { box-sizing: border-box; margin: 0; padding: 0; }
  html, body {
    width: 1200px; height: 800px; overflow: hidden;
    background: var(--backdrop);
    font-family: "Montserrat", sans-serif;
  }
  .sheet {
    width: 1200px; height: 800px;
    display: flex; flex-direction: column; align-items: center; justify-content: center;
    gap: 40px;
  }
  .card {
    position: relative;
    width: 560px; height: 320px;
    background: var(--card);
    border-radius: 22px;
    box-shadow: 0 3px 0 var(--edge), 0 12px 24px rgba(0,0,0,.25);
    overflow: hidden;
  }

  /* front */
  .brand-name {
    position: absolute; top: 30px; right: 34px; width: 240px;
    text-align: right;
    color: var(--silver); font-weight: 600; font-size: 13px;
    letter-spacing: .08em; line-height: 1.4; text-transform: uppercase;
  }

  .headshot {
    position: absolute; left: 34px; top: 58px;
    width: 108px; height: 108px; border-radius: 50%;
    border: 5px solid #f1f1f1;
    background: linear-gradient(180deg, var(--photo-top), var(--photo-bottom));
  }
  .identity { position: absolute; left: 158px; top: 116px; }
  .agent-name {
    color: var(--accent); font-weight: 700; font-size: 20px;
    text-transform: uppercase; letter-spacing: .02em; line-height: 1.2;
  }
  .agent-role { color: var(--muted); font-size: 12px; margin-top: 3px; }

  .divider {
    position: absolute; left: 34px; right: 34px; top: 182px;
    height: 1px; background: var(--accent);
  }

  .contact { position: absolute; left: 34px; top: 198px; list-style: none; }
  .contact li {
    display: flex; align-items: center; gap: 9px;
    color: var(--text); font-size: 13px; line-height: 24px;
  }
  .contact svg { width: 13px; height: 13px; fill: var(--accent); flex: none; }

  .office {
    position: absolute; right: 34px; top: 200px; text-align: right;
    font-style: normal;
    color: var(--text); font-size: 12px; line-height: 20px;
  }

  /* back */
  .card--back { display: flex; align-items: center; justify-content: center; }
  .back-name {
    width: 440px;
    color: var(--silver); font-weight: 600; text-transform: uppercase; text-align: center;
    letter-spacing: .08em; font-size: 26px; line-height: 1.35;
  }
</style>
</head>
<body>
<main class="sheet">
  <section class="card card--front" aria-label="Card front">
    <p class="brand-name">Harborline Realty<br>&amp; Investment Corp.</p>

    <div class="headshot" role="img" aria-label="Headshot of Miles Tandrow in a suit jacket"></div>
    <div class="identity">
      <h1 class="agent-name">Miles Tandrow</h1>
      <p class="agent-role">Real Estate Agent</p>
    </div>

    <div class="divider"></div>

    <ul class="contact">
      <li><svg viewBox="0 0 24 24"><path d="M6.6 10.8a15.1 15.1 0 0 0 6.6 6.6l2.2-2.2c.3-.3.7-.4 1-.2 1.1.4 2.3.6 3.6.6.6 0 1 .4 1 1V20c0 .6-.4 1-1 1A17 17 0 0 1 3 4c0-.6.4-1 1-1h3.5c.6 0 1 .4 1 1 0 1.3.2 2.5.6 3.6.1.3 0 .7-.2 1z"/></svg>801-555-0162</li>
      <li><svg viewBox="0 0 24 24"><path d="M2 5h20v14H2zm2 2v.5l8 5 8-5V7zm0 2.8V17h16V9.8l-8 5z"/></svg>miles@harborlinehomesite.com</li>
      <li><svg viewBox="0 0 24 24"><path d="M12 2a10 10 0 1 0 0 20 10 10 0 0 0 0-20zm6.9 9h-3a15 15 0 0 0-1.3-5.6A8 8 0 0 1 18.9 11zM12 4c.9 1.2 1.8 3.6 1.9 7h-3.8c.1-3.4 1-5.8 1.9-7zM9.4 5.4A15 15 0 0 0 8.1 11h-3a8 8 0 0 1 4.3-5.6zM5.1 13h3a15 15 0 0 0 1.3 5.6A8 8 0 0 1 5.1 13zm6.9 7c-.9-1.2-1.8-3.6-1.9-7h3.8c-.1 3.4-1 5.8-1.9 7zm2.6-1.4a15 15 0 0 0 1.3-5.6h3a8 8 0 0 1-4.3 5.6z"/></svg>HarborlineHomesite.com</li>
    </ul>

    <address class="office">
      Harborline Realty &amp; Investment Corp.<br>
      5286 N 7200 Suite 208-617<br>
      Cedar Hollow, UT 84190
    </address>
  </section>

  <section class="card card--back" aria-label="Card back">
    <p class="back-name">Harborline Realty &amp; Investment Corp.</p>
  </section>
</main>
</body>
</html>
```